1" x 3" label needed for essential oil bottle(s) - new ecommerce company

We need a label designed for 10 ml bottles of essential oils. We are offering 9 different types of essential oil: Lavender, Cedarwood, Eucalyptus, Frankincense, Lemon, Orange, Peppermint, Rosemary, and Tea Tree. The label should have a space for the type of essential oil. The bottles are an amber color (am including a photo) as essential oils are sensitive to light. also am including an AI file of our logo, which we'd like included on the label; the logo file also contains our logo colors, a dark blue and light grey. We'd also like the following on the label: "CAUTION: EYE AND SKIN IRRITANT. Avoid contact with eyes and skin. Wash hands after handling. If eye contact occurs, flush with water for 15 minutes. Not intended for topical or internal use. Contains Essential Oils. KEEP OUT OF REACH OF CHILDREN."
Also "Ingredients: 100% pure essential oil, GC tested."
Also "0.33 fl oz (10 ml)
Finally, we will need to include a sideways bar code on the right side of the label, so need 3/8" of white space on the right of the label.
We'd like the label to be calming, but modern, friendly, and confident.

```html
<!DOCTYPE html>
<html lang="en">
<head>
<meta charset="utf-8">
<title>Solvera Frankincense Label</title>
<link href="https://fonts.googleapis.com/css2?family=Playfair+Display:wght@400;600;700&family=Jost:wght@400;500;600&display=swap" rel="stylesheet">
<style>
  :root {
    --page: #f7f7f7;
    --label: #e5d2ba;
    --ink: #857a72;
    --light: #ffffff;
    --brand-blue: #1f2f4d;
    --brand-grey: #c9cbcf;
    --barcode-zone: #ffffff;
  }
  * { box-sizing: border-box; margin: 0; padding: 0; }
  html, body { width: 1200px; height: 1200px; overflow: hidden; }
  body {
    background: var(--page);
    display: flex;
    align-items: center;
    justify-content: center;
    font-family: "Jost", sans-serif;
    color: var(--ink);
    font-variant-numeric: lining-nums;
  }
  .label {
    width: 1080px;
    height: 400px;
    background: var(--label);
    display: flex;
    box-shadow: 0 2px 10px rgba(0,0,0,0.08);
  }
  .front {
    width: 470px;
    display: flex;
    flex-direction: column;
    align-items: center;
    justify-content: center;
  }
  .brand {
    display: flex;
    align-items: center;
    gap: 14px;
  }
  .brand-mark {
    width: 30px; height: 30px;
    background: var(--brand-grey);
    border-radius: 50%;
  }
  .brand-name {
    font-family: "Playfair Display", serif;
    font-weight: 400;
    font-size: 38px;
    letter-spacing: 9px;
    color: var(--brand-blue);
  }
  .rule { height: 2px; background: var(--ink); opacity: 0.8; }
  .front .rule.top { width: 300px; margin-top: 12px; }
  .sparkle { margin-top: 26px; width: 24px; height: 24px; }
  .oil-name {
    margin-top: 14px;
    font-family: "Playfair Display", serif;
    font-weight: 700;
    font-size: 46px;
    letter-spacing: 3px;
    color: var(--light);
  }
  .purity {
    margin-top: 26px;
    font-family: "Playfair Display", serif;
    font-size: 22px;
    letter-spacing: 1.5px;
    color: var(--ink);
  }
  .front .rule.bottom { width: 300px; margin-top: 6px; }
  .volume {
    margin-top: 18px;
    font-family: "Playfair Display", serif;
    font-size: 22px;
    color: var(--light);
    letter-spacing: 1px;
  }
  .back {
    width: 475px;
    padding: 30px 30px 0 32px;
    display: flex;
    flex-direction: column;
  }
  .ingredients { font-size: 18px; line-height: 1.3; }
  .ingredients strong {
    font-family: "Playfair Display", serif;
    font-weight: 600;
    font-size: 20px;
  }
  .back .rule { width: 100%; margin: 14px 0 12px; }
  .caution-title {
    font-family: "Playfair Display", serif;
    font-weight: 600;
    font-size: 20px;
    line-height: 1.2;
    letter-spacing: 1px;
  }
  .caution-sub {
    font-family: "Playfair Display", serif;
    font-size: 19px;
    letter-spacing: 1px;
  }
  .caution-text { margin-top: 4px; font-size: 15px; line-height: 1.35; color: var(--light); }
  .caution-text p + p { margin-top: 3px; }
  .keep-out {
    margin-top: 5px;
    font-weight: 600;
    font-size: 16px;
    color: var(--light);
    letter-spacing: 0.2px;
  }
  .back-foot {
    margin-top: 10px;
    display: flex;
    align-items: center;
    justify-content: space-between;
  }
  .site {
    font-family: "Playfair Display", serif;
    font-weight: 600;
    font-size: 21px;
    letter-spacing: 1px;
  }
  .badges { display: flex; gap: 10px; }
  .badge {
    width: 44px; height: 44px;
    border: 2px solid var(--ink);
    border-radius: 50%;
  }
  .barcode-zone { width: 135px; background: var(--barcode-zone); }
</style>
</head>
<body>
  <div class="label">
    <section class="front">
      <div class="brand">
        <span class="brand-mark"></span>
        <span class="brand-name">SOLVERA</span>
      </div>
      <div class="rule top"></div>
      <svg class="sparkle" viewBox="0 0 24 24" aria-hidden="true">
        <path d="M12 0 L14 10 L24 12 L14 14 L12 24 L10 14 L0 12 L10 10 Z" fill="#857a72"/>
      </svg>
      <h1 class="oil-name">Frankincense</h1>
      <div class="purity">100% PURE ESSENTIAL OIL</div>
      <div class="rule bottom"></div>
      <div class="volume">10ml ℮ 0.33fl.oz.</div>
    </section>

    <section class="back">
      <p class="ingredients"><strong>Ingredients:</strong> Frankincense (Boswellia Serrata Oil). GC tested.</p>
      <div class="rule"></div>
      <div class="caution-title">CAUTION:</div>
      <div class="caution-sub">EYE + SKIN IRRITANT</div>
      <div class="caution-text">
        <p>Avoid contact with eyes and skin. Wash hands after handling. If eye contact occurs, flush with water for 15 minutes.</p>
        <p>Not intended for topical or internal use. Contains Essential Oils.</p>
      </div>
      <div class="keep-out">KEEP OUT OF REACH OF CHILDREN.</div>
      <div class="back-foot">
        <span class="site">solvera.com</span>
        <div class="badges">
          <span class="badge" role="img" aria-label="Cruelty-free badge"></span>
          <span class="badge" role="img" aria-label="Recyclable badge"></span>
        </div>
      </div>
    </section>

    <div class="barcode-zone"></div>
  </div>
</body>
</html>
```